RM Tomás Ledesma (Business Card)

Hi designers, in this work, I'm looking for an sophisticated stylish, elegant and proffesional personal card. We have a laboratory of pathology automated, with equipments high quality.
In this web the designers, have created my business logo, the name is "RM Tomás Ledesma"
In our lab, we principal work is to prepare the biopsies for further diagnostic of diseases like cancer, tumors, etc.
I need that the first face, only having my complete logo (Rm Tomás Ledesma, Laboratorio de procesamiento Histologico)
The overleaf, could repeat the same logo, like water logo.
In this face, I need to say: My full data:

Técnico en Anatomía Patológica
Tomás Ledesma Urquiza M.P 48213
Av. Duarte Quirós 817 - 2do piso - Instituto Brandsen.
Córdoba, Argentina
(0351) 158246093
ledesma.tomas@correoviva.com.ar

with respect the colors of card, use your imagination, the original logo color is violet, I haven't chosen a color base for the card.

attached pictures are examples of cards I like your DESIGN.
Attached too, the original logo to my company.

the size of card are:
horizontal: 9cm
vertical: 5,5cm

any question that you have, not doubt to question me,
Hand to work!

Industry/Entity Type

Laboratory

Requirements
Must have
• designers sophisticated, not simples, like show the images attached

```html
<!DOCTYPE html>
<html lang="es">
<head>
<meta charset="utf-8">
<title>Tomás Ledesma – Tarjeta personal</title>
<link rel="stylesheet" href="https://fonts.googleapis.com/css2?family=Roboto:wght@300;400;700&family=Roboto+Condensed:wght@400&display=swap">
<style>
  :root {
    --violet: #8a34bf;
    --violet-light: #a04fd6;
    --violet-dark: #6a1c9c;
    --paper: #ffffff;
    --backdrop: #eeeef0;
    --ink-grey: #7a7a7e;
    --ink-violet: #7b2cb0;
  }
  html, body {
    margin: 0;
    width: 1200px;
    height: 1023px;
    overflow: hidden;
    background: var(--backdrop);
    font-family: "Roboto", Arial, sans-serif;
  }
  .business-card {
    position: absolute;
    left: 150px;
    top: 236px;
    width: 900px;
    height: 550px;
    border-radius: 18px;
    overflow: hidden;
    background: var(--paper);
    box-shadow: 0 10px 30px rgba(0,0,0,0.18);
  }
  .brand-panel {
    position: absolute;
    left: 0;
    top: 0;
    width: 420px;
    height: 100%;
    background: radial-gradient(ellipse at 55% 50%, var(--violet-light) 0%, var(--violet) 45%, var(--violet-dark) 100%);
  }
  .brand-lockup {
    position: absolute;
    left: 60px;
    top: 330px;
    width: 300px;
    color: var(--paper);
    text-align: left;
  }
  .brand-mark {
    display: inline-block;
    width: 16px;
    height: 16px;
    border: 2px solid var(--paper);
    vertical-align: middle;
    margin-right: 10px;
  }
  .brand-name {
    font-family: "Roboto Condensed", Arial, sans-serif;
    font-weight: 400;
    font-size: 24px;
    letter-spacing: 3px;
    text-transform: uppercase;
    vertical-align: middle;
  }
  .brand-tagline {
    margin-top: 10px;
    font-family: "Roboto Condensed", Arial, sans-serif;
    font-size: 15px;
    letter-spacing: 0.5px;
    text-transform: uppercase;
  }
  .contact-icons {
    position: absolute;
    left: 0;
    top: 0;
    width: 460px;
    height: 550px;
  }
  .contact-block {
    position: absolute;
    left: 470px;
    top: 60px;
    width: 400px;
  }
  .holder-name {
    margin: 0;
    font-weight: 700;
    font-size: 25px;
    color: var(--ink-violet);
  }
  .holder-title {
    margin: 4px 0 0;
    font-weight: 300;
    font-size: 17px;
    color: var(--ink-grey);
  }
  .contact-line {
    position: absolute;
    left: 470px;
    margin: 0;
    font-weight: 400;
    font-size: 18px;
    line-height: 27px;
    color: var(--ink-grey);
  }
  .contact-address { top: 188px; }
  .contact-phone   { top: 300px; }
  .contact-email   { top: 378px; }
</style>
</head>
<body>
  <div class="business-card">
    <div class="brand-panel">
      <div class="brand-lockup">
        <span class="brand-mark"></span><span class="brand-name">Tomás Ledesma</span>
        <div class="brand-tagline">Laboratorio de procesamiento histológico</div>
      </div>
    </div>

    <svg class="contact-icons" viewBox="0 0 460 550" aria-hidden="true">
      <!-- divider notches -->
      <polygon points="420,194 436,210 420,226" fill="#8a34bf"/>
      <polygon points="420,300 436,316 420,332" fill="#8a34bf"/>
      <polygon points="420,376 436,392 420,408" fill="#8a34bf"/>
      <!-- pin -->
      <circle cx="370" cy="210" r="21" fill="#ffffff"/>
      <path d="M370 199 a7 7 0 0 1 7 7 c0 6 -7 14 -7 14 c0 0 -7 -8 -7 -14 a7 7 0 0 1 7 -7z" fill="#8a34bf"/>
      <circle cx="370" cy="206" r="2.6" fill="#ffffff"/>
      <!-- phone -->
      <circle cx="370" cy="316" r="21" fill="#ffffff"/>
      <rect x="363" y="304" width="14" height="24" rx="2.5" fill="none" stroke="#8a34bf" stroke-width="2.2"/>
      <circle cx="370" cy="324" r="1.6" fill="#8a34bf"/>
      <!-- mail -->
      <circle cx="370" cy="392" r="21" fill="#ffffff"/>
      <rect x="359" y="384" width="22" height="16" fill="none" stroke="#8a34bf" stroke-width="2"/>
      <polyline points="359,384 370,393 381,384" fill="none" stroke="#8a34bf" stroke-width="2"/>
    </svg>

    <div class="contact-block">
      <h1 class="holder-name">Tomás Ledesma Urquiza M.P 48213</h1>
      <p class="holder-title">Técnico en Anatomía Patológica</p>
    </div>
    <p class="contact-line contact-address">Av. Duarte Quirós 817 - 2do piso -<br>Instituto Brandsen.<br>Córdoba, Argentina</p>
    <p class="contact-line contact-phone">(0351) 158246093</p>
    <p class="contact-line contact-email">ledesma.tomas@correoviva.com.ar</p>
  </div>
</body>
</html>
```